Meridale Bed Company Needs Business Card

Looking for a very nice looking business card. Creative but not extravagant. We sell beds and pillows across the U.S. and need something professional but catchy. I have attached the logo.

Name : Devin Holt
Title : President
Phone : (800) 471-2960
Email: sleep@quilmora.com
Website: www.quilmora.com

Can be single-sided or double-sided
horizontal or vertical

Can use Blues/Greys

Target Market(s)

Mass Market

Industry/Entity Type

Retail

Contact Information for Business Card

Name : Devin Holt
Title : President
Phone : (800) 471-2960
Email: sleep@quilmora.com
Website: www.quilmora.com

Requirements
Must have
• Clean, Modern, Smooth
• Can use Blues/Greys
• On the other side without the information - have something simple like www.quilmora.com or our logo
Nice to have
• Surprise me
Should not have
• Nothing crazy, nothing cluttered

```html
<!DOCTYPE html>
<html lang="en">
<head>
<meta charset="utf-8">
<title>Quilmora Business Card</title>
<link rel="stylesheet" href="https://fonts.googleapis.com/css2?family=Quicksand:wght@400;500;600&display=swap">
<style>
  :root {
    --backdrop: #dfe2e3;
    --brand-blue: #4dd0f4;
    --card-white: #ffffff;
    --ink: #3a3a3a;
    --shadow: rgba(0, 0, 0, 0.22);
  }
  * { margin: 0; padding: 0; box-sizing: border-box; }
  html, body {
    width: 1200px;
    height: 763px;
    overflow: hidden;
    background: var(--backdrop);
    font-family: "Quicksand", sans-serif;
  }
  .stage { position: relative; width: 1200px; height: 763px; }
  .card {
    position: absolute;
    width: 400px;
    height: 230px;
    box-shadow: 6px 7px 8px var(--shadow);
  }
  .card-front {
    left: 153px; top: 271px;
    background: var(--brand-blue);
    display: flex; align-items: center; justify-content: center;
  }
  .card-front .wordmark {
    color: var(--card-white);
    font-size: 52px;
    font-weight: 400;
    letter-spacing: 1px;
    margin-top: -12px;
  }
  .card-back {
    left: 617px; top: 274px;
    background: var(--card-white);
  }
  .card-back .wordmark {
    position: absolute;
    left: 50px; top: 36px;
    color: var(--brand-blue);
    font-size: 38px;
    font-weight: 400;
    letter-spacing: 0.5px;
    line-height: 1;
  }
  .website {
    position: absolute;
    left: 51px; top: 146px;
    color: var(--brand-blue);
    font-size: 13px;
    font-weight: 500;
    letter-spacing: 0.3px;
  }
  .social-row {
    position: absolute;
    left: 52px; top: 170px;
  }
  .contact {
    position: absolute;
    left: 254px; top: 56px;
    color: var(--ink);
    font-size: 11px;
    font-weight: 500;
    letter-spacing: 0.3px;
  }
  .contact .name { color: var(--brand-blue); font-weight: 600; line-height: 14px; }
  .contact .title { line-height: 14px; }
  .contact .divider {
    width: 13px; height: 3px;
    background: var(--brand-blue);
    margin: 7px 0 8px;
  }
  .contact .details li { list-style: none; line-height: 18.8px; }
</style>
</head>
<body>
<main class="stage">
  <section class="card card-front">
    <span class="wordmark">quilmora</span>
  </section>

  <section class="card card-back">
    <span class="wordmark">quilmora</span>
    <span class="website">www.quilmora.com</span>
    <svg class="social-row" width="140" height="20" viewBox="0 0 140 20" aria-label="Social media links">
      <circle cx="10" cy="9" r="9" fill="var(--brand-blue)"/>
      <circle cx="37" cy="9" r="9" fill="var(--brand-blue)"/>
      <circle cx="63" cy="9" r="9" fill="var(--brand-blue)"/>
      <circle cx="89" cy="9" r="9" fill="var(--brand-blue)"/>
      <circle cx="114" cy="9" r="9" fill="var(--brand-blue)"/>
    </svg>
    <div class="contact">
      <p class="name">Devin Holt</p>
      <p class="title">President</p>
      <div class="divider"></div>
      <ul class="details">
        <li>T. (800) 471-2960</li>
        <li>E. sleep@quilmora.com</li>
        <li>W. www.quilmora.com</li>
        <li>14 Harlow Lane,</li>
        <li>Brookfield NSW 2071</li>
      </ul>
    </div>
  </section>
</main>
</body>
</html>
```